Lev Marchetti - Senior Living Audio CDs - CD Design and Cover Design

I am an executive director in an assisted living facility. I have just started speaking, training, and coaching in the Senior Living Industry. I have 4 audio files that I want to put to a CD. The names of the CD's are:

1- Leadership - Creating A Culture of Excellence in Senior Living
2- The Purpose of Your Senior Living Business
3- A Leaders Vision - Your Attention Becomes Your Intention
4- Group Interviews -A Secret in Employee Retention

I think I can use the same CD cover for each CD. I just need the same design but 4 different ones with the names above. So everything will be the same but the name change. The inside cover will be I will consider other colors but it would be great if it would look good with the logo. I also need help with designing the CD face itself. I will be using a standard Jewel CD case. I need the front cover, the inside cover, and the back. The logo will be on all three.

On the front:

Part of me thinks it should be a clean simple design with my logo, my picture, and the title. But I am also curious about the picture of me with the elderly lady. - I need the 4 designs that are the same except the title.

On the Inside:

It can be the same design but the wording will be specific to that CD and the 4 insides will be:

All businesses rise and fall with leadership. This is especially true in the senior living industry. The life of that rise or fall is based on the culture the leader creates. Learn the 3 keys to what leaders know and do. Learn what the Importance Factor is and how you can put it to work to create and sustain a winning culture that will drive your business and occupancy above the rest.

What is the purpose of your senior living business? Your understanding to the answer of this question makes all the difference. After you have gained this understanding it takes the right beliefs and behavior of associates to fulfill this purpose. What's the purpose? How is it fulfilled?

They want a captain not a boss. As a leader in senior living you steer the ship. What you put your attention on becomes the intention of your community. Your ability to create a vision, help people embrace that vision, and learn how to stay focused when the storms of the industry come raging, is the key to your success. There is a pattern to achieving this success. Come learn this pattern and how to apply it in your life and your business. It can make all the difference.

A business can not be better than it's people. The right people are the key not just people. Learn where your focus should be to hire the right people. After you hire then find out what you can do to retain them and engage them. If you want happy residents you need happy associates.

On the back it will need to have:

1- My Logo
2- www.LevMarchetti.example
3- Email: info@LevMarchetti.example
4- You could put the picture of me and the elderly lady as a watermark on the back with the above info.

I have a short turn around time and need designs quickly. I also need help with designing the CD. My picture, the logo, and the Title.

```html
<!DOCTYPE html>
<html lang="en">
<head>
<meta charset="utf-8">
<title>Lev Marchetti – Leadership CD Insert and Disc</title>
<link rel="stylesheet" href="https://fonts.googleapis.com/css2?family=Nunito+Sans:wght@400;600&family=Marcellus&display=swap">
<style>
  :root {
    --page: #eeeeec;
    --insert-top: #3a3a3a;
    --insert-bottom: #2a2a2a;
    --cream: #ece0b8;
    --gold: #c9b27a;
    --gold-dark: #8c7744;
    --text-light: #f2f2f2;
    --text-muted: #a8a8a8;
    --title-faint: #6e6e6e;
    --disc: #3b3b3b;
    --disc-edge: #2b2b2b;
  }
  * { box-sizing: border-box; margin: 0; padding: 0; }
  html, body { width: 1200px; height: 800px; overflow: hidden; }
  body {
    background: var(--page);
    position: relative;
    font-family: "Nunito Sans", Arial, sans-serif;
  }

  /* Inside cover */
  .insert {
    position: absolute;
    left: 70px;
    top: 120px;
    width: 480px;
    height: 560px;
    background: linear-gradient(180deg, var(--insert-top), var(--insert-bottom));
    box-shadow: 0 10px 30px rgba(0,0,0,0.18);
    overflow: hidden;
  }
  .insert__headline {
    position: absolute;
    left: 40px;
    top: 70px;
    width: 260px;
    color: var(--text-light);
    font-weight: 600;
    font-size: 15px;
    line-height: 1.45;
    text-align: center;
  }
  .insert__body {
    position: absolute;
    left: 40px;
    top: 130px;
    width: 260px;
    color: var(--text-muted);
    font-size: 11.5px;
    line-height: 1.6;
    text-align: center;
  }
  .insert__portrait {
    position: absolute;
    left: 315px;
    top: 20px;
    width: 140px;
    height: 400px;
    border-radius: 60px 60px 20px 20px;
    background: linear-gradient(180deg, #5a5a5a 0%, #454545 60%, #383838 100%);
  }
  .insert__title {
    position: absolute;
    left: 40px;
    top: 400px;
    color: var(--title-faint);
    font-family: "Marcellus", Georgia, serif;
    font-size: 30px;
    letter-spacing: 4px;
  }
  .insert__byline {
    position: absolute;
    right: 30px;
    top: 440px;
    color: var(--title-faint);
    font-size: 10px;
    line-height: 1.4;
    text-align: right;
  }
  .insert__band {
    position: absolute;
    left: 0;
    bottom: 0;
    width: 100%;
    height: 70px;
    background: var(--cream);
    display: flex;
    align-items: center;
    justify-content: center;
  }
  .brand-mark {
    display: flex;
    align-items: center;
    gap: 8px;
    font-family: "Nunito Sans", Arial, sans-serif;
    font-weight: 600;
    font-size: 13px;
    color: var(--gold-dark);
    letter-spacing: 1px;
  }
  .brand-mark__dot {
    width: 14px;
    height: 14px;
    border-radius: 50%;
    background: var(--gold-dark);
  }

  /* Disc */
  .disc {
    position: absolute;
    left: 620px;
    top: 140px;
    width: 520px;
    height: 520px;
  }
  .disc__title {
    font-family: "Marcellus", Georgia, serif;
    font-size: 34px;
    letter-spacing: 5px;
    fill: #9d9d9d;
  }
  .disc__brand {
    font-family: "Nunito Sans", Arial, sans-serif;
    font-weight: 600;
    font-size: 16px;
    fill: var(--gold);
    letter-spacing: 1px;
  }
</style>
</head>
<body>

  <section class="insert" aria-label="Inside cover">
    <h1 class="insert__headline">All Businesses Rise<br>And Fall With Leadership</h1>
    <p class="insert__body">This is especially true in the senior living industry. The life of that rise or fall is based on the culture the leader creates. Learn the 3 keys to what leaders know and do. Learn what the importance factor is and how you can put it to work to create and sustain a winning culture that will drive your business and occupancy above the rest.</p>
    <div class="insert__portrait" role="img" aria-label="Full-length portrait of Lev Marchetti in a dark suit"></div>
    <p class="insert__title">LEADERSHIP</p>
    <p class="insert__byline">By Executive Director,<br>Lev Marchetti</p>
    <div class="insert__band">
      <span class="brand-mark"><span class="brand-mark__dot"></span>Lev Marchetti</span>
    </div>
  </section>

  <svg class="disc" viewBox="0 0 520 520" aria-label="Disc face: 1. Leadership">
    <defs>
      <radialGradient id="discFace" cx="45%" cy="40%" r="65%">
        <stop offset="0%" stop-color="#474747"/>
        <stop offset="100%" stop-color="#2f2f2f"/>
      </radialGradient>
      <radialGradient id="hubShine" cx="50%" cy="50%" r="50%">
        <stop offset="0%" stop-color="#d9d9d9"/>
        <stop offset="100%" stop-color="#8a8a8a"/>
      </radialGradient>
    </defs>
    <circle class="disc__edge" cx="260" cy="260" r="258" fill="var(--cream)"/>
    <circle cx="260" cy="260" r="250" fill="var(--gold)"/>
    <circle cx="260" cy="260" r="243" fill="url(#discFace)"/>
    <circle cx="260" cy="260" r="72" fill="#2a2a2a"/>
    <circle cx="260" cy="260" r="62" fill="url(#hubShine)"/>
    <circle cx="260" cy="260" r="40" fill="#1f1f1f"/>
    <circle cx="260" cy="260" r="18" fill="var(--page)"/>
    <text class="disc__title" x="260" y="370" text-anchor="middle">1. LEADERSHIP</text>
    <circle cx="196" cy="418" r="8" fill="var(--gold)"/>
    <text class="disc__brand" x="212" y="424">Lev Marchetti</text>
  </svg>

</body>
</html>
```